"Vine Hollow Excursions" is a top notch Santa Barbara County Wine Tour company.

We provide scenic, boutique and custom wine tours. I need the card to be clean and classy. I will provide our logo. I would like the logo to cover the back side of the card as an option and would like to see a couple color options other then our signature green and gold. I would like to see some creative options and let the designers come up with options.
I need cards for myself and my team. The final design should communicate "An authentic and boutique wine tour experience"
Please use my website for reference www.vinehollowexcursions.example

Target Market(s)

We have a wide range of clients from millennials to baby boomers

Industry/Entity Type

Tour

Contact Information for Business Card

Contact info:
Dale Morton
805-219-6384
info@vinehollowexcursions.example
vinehollowexcursions.example

Colors

Designer to choose colors to be used in the design.

Requirements
Must have
• my logo
Nice to have
• *I would like to have the backside side with the logo and the company statement
• "An authentic and boutique wine tour experience" as an option.
• *I would also like to see what the designers can create!
• *I would like to see an option that incorporates or social: instagram, yelp, trip advisor
Should not have
• I do not want it too busy.

```html
<!DOCTYPE html>
<html lang="en">
<head>
<meta charset="utf-8">
<title>Vine Hollow Excursions – Business Card</title>
<link rel="stylesheet" href="https://fonts.googleapis.com/css2?family=Cinzel:wght@400;500&family=Source+Sans+3:wght@400;600&display=swap">
<style>
  :root {
    --backdrop: #2b2b2b;
    --card-white: #f4f4f2;
    --vine-green: #276140;
    --gold: #8a6a4a;
    --text-light: #ffffff;
    --rule-light: rgba(255,255,255,0.75);
    --tan-center: #b29d7c;
    --tan-edge: #776a59;
    --badge-fill: #e8e3d8;
    --mark-fill: rgba(255,255,255,0.85);
  }
  * { margin: 0; padding: 0; box-sizing: border-box; }
  html, body { width: 1200px; height: 960px; overflow: hidden; }
  body { background: var(--backdrop); position: relative; }

  .card {
    position: absolute;
    width: 600px;
    height: 343px;
    overflow: hidden;
  }

  /* Front side */
  .card--front { left: 314px; top: 113px; background: var(--card-white); }
  .front__scene {
    position: absolute; left: 0; top: 0; width: 600px; height: 343px; display: block;
  }
  .brand-lockup--front {
    position: absolute; right: 28px; top: 34px;
    display: flex; align-items: center; gap: 10px;
  }
  .brand-lockup__mark--front {
    width: 14px; height: 14px; border-radius: 50%; background: var(--gold);
  }
  .brand-name--front {
    font-family: "Cinzel", serif; font-weight: 500; font-size: 20px;
    color: var(--gold); letter-spacing: 0.5px;
  }
  .person-name {
    position: absolute; left: 0; width: 600px; top: 221px;
    text-align: center;
    font-family: "Cinzel", serif; font-weight: 400; font-size: 25px;
    color: var(--text-light); letter-spacing: 0.5px;
  }
  .contact-line {
    position: absolute; left: 0; width: 600px; top: 255px;
    text-align: center; white-space: nowrap;
    font-family: "Source Sans 3", sans-serif; font-size: 13.5px;
    color: var(--text-light);
  }
  .tagline {
    position: absolute; left: 0; width: 600px; top: 277px;
    text-align: center;
    font-family: "Source Sans 3", sans-serif; font-weight: 600; font-size: 15px;
    color: var(--text-light);
  }
  .social-row {
    position: absolute; left: 95px; top: 304px; width: 420px; height: 22px;
    display: flex; align-items: center; gap: 8px;
  }
  .social-row__rule {
    flex: 1; height: 1px;
    background: linear-gradient(90deg, transparent, var(--rule-light));
  }
  .social-row__rule--right { background: linear-gradient(90deg, var(--rule-light), transparent); }
  .social-row__badge {
    width: 22px; height: 22px; border-radius: 3px; background: var(--badge-fill);
  }

  /* Back side */
  .card--back {
    left: 311px; top: 472px;
    background: radial-gradient(ellipse 60% 75% at 52% 30%, var(--tan-center) 0%, var(--tan-edge) 100%);
    display: flex; flex-direction: column; align-items: center; justify-content: center;
    gap: 22px;
  }
  .brand-lockup__mark--back {
    width: 84px; height: 84px; border-radius: 50%; background: var(--mark-fill);
    margin-top: 10px;
  }
  .brand-name--back {
    font-family: "Cinzel", serif; font-weight: 500; font-size: 32px;
    color: var(--text-light); letter-spacing: 1px;
  }
</style>
</head>
<body>
  <section class="card card--front">
    <svg class="front__scene" viewBox="0 0 600 343" role="img" aria-label="Illustration of a rising sun with rays behind green mountain ridges">
      <path d="M0 220 C120 190 220 140 330 132 C420 128 500 170 600 200 L600 343 L0 343 Z" fill="var(--vine-green)"/>
    </svg>
    <div class="brand-lockup--front">
      <span class="brand-lockup__mark--front"></span>
      <p class="brand-name--front">Vine Hollow Excursions</p>
    </div>
    <h1 class="person-name">DALE MORTON</h1>
    <p class="contact-line">805-219-6384 |info@vinehollowexcursions.example |vinehollowexcursions.example</p>
    <p class="tagline">An authentic &amp; boutique wine tour experience</p>
    <div class="social-row">
      <span class="social-row__rule"></span>
      <span class="social-row__badge"></span>
      <span class="social-row__badge"></span>
      <span class="social-row__badge"></span>
      <span class="social-row__rule social-row__rule--right"></span>
    </div>
  </section>

  <section class="card card--back">
    <span class="brand-lockup__mark--back"></span>
    <p class="brand-name--back">Vine Hollow Excursions</p>
  </section>
</body>
</html>
```